Buch-/E-Book-Cover im Bereich der Persönlichkeitsentwicklung
Vielen lieben Dank für die super Arbeit von Dir. Das Design ist klasse und die vielen Vorschläge waren auch super. Die komplette Zusammenarbeit verlief sehr professionell und Änderungswünsche wurden sehr schnell umgesetzt. Ich kann Dich voll und ganz weiterempfehlen.
Zielgruppe
Wir arbeiten in der Persönlichkeitsentwicklung für Jugendliche. Dabei spezialisieren wir uns auf den Altersbereich 12 - 17 Jahre. Unser Ziel ist es jungen Menschen zu zeigen, wie Sie zu sich selbst finden und ein glückliches sowie erfolgreiches Leben führen können.
Aufgabenstellung
- Das Design sollte für die Eltern von Teenagern und auch für die Teenager selbst ausgelegt werden. Das Buch ist für die Jugendlichen (Mädchen und Jungen im Alter zwischen 12 Jahren und 17 Jahren) gedacht, wird allerdings meist von deren Mütter gekauft.
- Der Name des Autors lautet: Henrik Falbe
- Der Titel lautet: Junge Herzen finden Mut und Richtung
- Der Untertitel lautet: Was Heranwachsende über ihren Weg lernen
- Im Anhang befinden sich Designs, die ich gut finde (nur falls jemand weitere Ideen haben möchte)
- Format: 15,24 cm x 22,86 cm (6' x 9') [genaue Maße fürs Taschenbuch und Hardcover sind im Anhang (.zip Dateien)]
1. E-Book:
- Coverdateien sollten idealerweise 2 560 Pixel hoch und 1 600 Pixel breit sein. Zur Gewährleistung der bestmöglichen Qualität (insbesondere auf HD-Geräten) sollte das Bild mindestens 2 500 Pixel hoch sein.
- Format: TIFF (.tif/.tiff) oder JPEG (.jpeg/.jpg)
- DPI: 72 dpi
- Größe: Ihr Coverbild muss kleiner als 50 MB sein.
Hinweis: Vermeiden Sie es, Ihre Dateien zu komprimieren. Dies kann die Qualität Ihres Covers auf Lesegeräten beeinträchtigen. Das beste Ergebnis erzielen Sie mit Bildern, die eine Mindestauflösung von 300 ppi (Pixels per Inch) haben.
- Rahmen: Coverbilder mit weißem oder sehr hellem Hintergrund heben sich kaum vom weißen Hintergrund ab. Fügen Sie einen dünnen Rahmen (3–4 Pixel) in Mittelgrau hinzu, um die Ränder des Covers besser sichtbar zu machen.
2. + 3. Taschenbuch/Hardcover [genaue Maße fürs Taschenbuch und Hardcover sind im Anhang (.zip Dateien)] :
- Dateityp: Das Cover muss als einzelne PDF-Datei vorliegen und die hintere Coverseite, den Buchrücken und die vordere Coverseite als einzelnes Bild enthalten.
- Dateigröße: Coverdateien, die größer als 650 MB sind, können nicht konvertiert werden. Die Datei sollte maximal 40 MB groß sein, da sich bei großen Dateien der Druck verlangsamt.
- Die gen..

```html
<!DOCTYPE html>
<html lang="de">
<head>
<meta charset="utf-8">
<title>Junge Herzen finden Mut und Richtung – Henrik Falbe</title>
<link rel="stylesheet" href="https://fonts.googleapis.com/css2?family=Dosis:wght@600&family=Montserrat:wght@400&family=Lexend:wght@600&display=swap">
<style>
  :root {
    --backdrop: #4aa22f;
    --paper: #f6f5f2;
    --author: #e0960e;
    --title: #0a3a84;
    --subtitle: #c8102e;
    --shirt: #f7b142;
    --hair: #1a1a1a;
    --skin: #ffffff;
    --leaf: #3a8f2f;
  }
  html, body {
    margin: 0;
    padding: 0;
    width: 1200px;
    height: 1200px;
    overflow: hidden;
    background: var(--backdrop);
  }
  .book-cover {
    position: absolute;
    left: 224px;
    top: 57px;
    width: 763px;
    height: 1080px;
    background: var(--paper);
    overflow: hidden;
    box-shadow: 14px 16px 22px rgba(20, 60, 10, 0.45);
  }
  .cover-author {
    position: absolute;
    top: 36px;
    width: 100%;
    margin: 0;
    text-align: center;
    font-family: "Montserrat", sans-serif;
    font-weight: 400;
    font-size: 48px;
    letter-spacing: 3px;
    line-height: 1;
    color: var(--author);
    text-transform: uppercase;
  }
  .cover-title {
    position: absolute;
    top: 80px;
    width: 100%;
    margin: 0;
    text-align: center;
    font-family: "Dosis", sans-serif;
    font-weight: 600;
    font-size: 78px;
    line-height: 92px;
    color: var(--title);
  }
  .cover-subtitle {
    position: absolute;
    top: 277px;
    width: 100%;
    margin: 0;
    text-align: center;
    font-family: "Lexend", sans-serif;
    font-weight: 600;
    font-size: 23px;
    letter-spacing: 1px;
    line-height: 1;
    color: var(--subtitle);
  }
  .cover-illustration {
    position: absolute;
    left: 0;
    top: 334px;
    width: 763px;
    height: 746px;
    background: linear-gradient(180deg,
      var(--paper) 0%,
      var(--hair) 14%,
      var(--hair) 30%,
      var(--skin) 46%,
      var(--skin) 58%,
      var(--shirt) 72%,
      var(--leaf) 84%,
      var(--shirt) 95%,
      var(--shirt) 100%);
  }
</style>
</head>
<body>
  <main class="book-cover">
    <p class="cover-author">Henrik Falbe</p>
    <h1 class="cover-title">Junge Herzen finden<br>Mut und Richtung</h1>
    <p class="cover-subtitle">Was Heranwachsende über ihren Weg lernen</p>
    <div class="cover-illustration" role="img" aria-label="Illustration: junge Person mit dunklem Bob-Haarschnitt und gelbem Shirt hält mit geschlossenen Augen ein grünes vierblättriges Kleeblatt vor der Brust"></div>
  </main>
</body>
</html>
```